The quiet harbor with an elephant incorporated in the background

Target Market(s)

Real estate

Industry/Entity Type

Real Estate

Contact Information for Business Card

On back on want my name & number
In front I want the business name, "the quiet harbor", below to say staging & design

Logo Text

The quiet harbor

Font styles to use
Serif

Colors
000000

Requirements
Must have
• I want an elephant behind the writing in gold transperant

```html
<!DOCTYPE html>
<html lang="en">
<head>
<meta charset="utf-8">
<title>The Quiet Harbor – Business Card</title>
<link rel="stylesheet" href="https://fonts.googleapis.com/css2?family=Alegreya:wght@400&family=Arimo:wght@400;700&display=swap">
<style>
  :root {
    --backdrop: #4a4a4a;
    --card: #050505;
    --accent: #f39019;
    --ink-light: #f2f2f2;
    --card-edge: #d8d8d8;
  }
  * { margin: 0; padding: 0; box-sizing: border-box; }
  html, body { width: 1200px; height: 1200px; overflow: hidden; }
  body {
    background: var(--backdrop);
    font-family: "Arimo", Arial, sans-serif;
    display: flex;
    flex-direction: column;
    align-items: center;
    justify-content: center;
    gap: 70px;
  }
  .card {
    position: relative;
    width: 840px;
    height: 480px;
    background: var(--card);
    border-bottom: 3px solid var(--card-edge);
    box-shadow: 0 14px 30px rgba(0,0,0,0.45);
  }
  .brand {
    display: flex;
    flex-direction: row-reverse;
    align-items: center;
    gap: 18px;
    color: var(--accent);
    font-family: "Alegreya", Georgia, serif;
    font-weight: 400;
  }
  .brand-mark {
    width: 46px;
    height: 46px;
    border-radius: 50%;
    background: var(--accent);
    flex: none;
  }
  .brand-text { display: flex; flex-direction: column; }
  .brand-name {
    font-size: 46px;
    letter-spacing: 0.5px;
    line-height: 1.05;
    white-space: nowrap;
  }
  .brand-tagline {
    font-size: 26px;
    letter-spacing: 2px;
    line-height: 1.1;
    white-space: nowrap;
  }
  /* Front */
  .card--front .brand {
    position: absolute;
    left: 170px;
    top: 180px;
  }
  /* Back */
  .card--back .brand {
    position: absolute;
    right: 50px;
    top: 60px;
  }
  .card--back .brand-name { font-size: 40px; }
  .card--back .brand-tagline { font-size: 22px; }
  .rule {
    position: absolute;
    left: 0;
    top: 150px;
    width: 640px;
    height: 2px;
    background: var(--accent);
  }
  .contact {
    position: absolute;
    left: 60px;
    top: 210px;
  }
  .contact-name {
    color: var(--accent);
    font-weight: 700;
    font-size: 40px;
    letter-spacing: 1px;
  }
  .contact-phone {
    color: var(--ink-light);
    font-weight: 400;
    font-size: 22px;
    margin-top: 10px;
  }
</style>
</head>
<body>
  <section class="card card--front">
    <div class="brand">
      <span class="brand-mark"></span>
      <div class="brand-text">
        <span class="brand-name">The Quiet Harbor</span>
        <span class="brand-tagline">staging &amp; design</span>
      </div>
    </div>
  </section>

  <section class="card card--back">
    <div class="rule"></div>
    <div class="brand">
      <span class="brand-mark"></span>
      <div class="brand-text">
        <span class="brand-name">The Quiet Harbor</span>
        <span class="brand-tagline">staging &amp; design</span>
      </div>
    </div>
    <div class="contact">
      <p class="contact-name">JANE MARLOW</p>
      <p class="contact-phone">T: 1-555-014-2290</p>
    </div>
  </section>
</body>
</html>
```